Business Card Design Project

We are not a new company, but renamed to "Vantorin Kitchens" last year. We specialize in modern high-end cabinetry imports. We would like to communicate a sense of quality and cutting edge technology. Ideally the design would incorporate our logo colors, silver, red and preferably a black, matte background. Though we are open to suggestions.
Logo is attached.
Edit: I have attached rough drafts of the previous cards, this way you will have all necessary content that needs to go on the cards.
Updates
Project Deadline Extended
Reason: We have received a lot of great designs, but due to the sheer number we couldn't respond to all. We will extend the deadline for another 7 days to finalize and provide feedback to designers.
Thank you for your hard work!
Industry/Entity Type
Business
Look and feel
Each slider illustrates characteristics of the customer's brand and the style your logo design should communicate.

```html
<!DOCTYPE html>
<html lang="en">
<head>
<meta charset="utf-8">
<title>Vantorin Kitchens – Business Cards</title>
<link href="https://fonts.googleapis.com/css2?family=Arimo:wght@400;700&display=swap" rel="stylesheet">
<style>
  :root {
    --stage: #b07a4a;
    --label: #2a1a0e;
    --card-black: #141414;
    --card-carbon: #1e1f21;
    --silver: #c9cbcf;
    --silver-dark: #9a9ca0;
    --red: #e0262b;
    --white: #ffffff;
    --ink: #1a1a1a;
  }
  * { box-sizing: border-box; margin: 0; padding: 0; }
  html, body {
    width: 1200px; height: 788px; overflow: hidden;
    background: var(--stage);
    font-family: "Arimo", Arial, sans-serif;
  }
  .sheet { position: relative; width: 1200px; height: 788px; }

  .view-label {
    position: absolute; width: 526px; text-align: center;
    font-size: 21px; color: var(--label);
  }

  .card {
    position: absolute; width: 526px; height: 301px;
    border-radius: 18px; overflow: hidden;
    box-shadow: 0 4px 10px rgba(0,0,0,.45);
  }
  .card--carbon { background: linear-gradient(180deg, #26272a 0%, var(--card-carbon) 55%, #101112 100%); }
  .card--matte { background: var(--card-black); }

  .card__wave { position: absolute; inset: 0; width: 100%; height: 100%; }

  .brand {
    position: absolute; display: flex; align-items: center; gap: 10px;
    font-weight: 700; color: var(--silver); letter-spacing: 1px; white-space: nowrap;
  }
  .brand__mark { background: var(--silver); flex: none; }
  .brand--front { left: 32px; top: 90px; font-size: 22px; }
  .brand--front .brand__mark { width: 20px; height: 20px; }
  .brand--back { left: 0; right: 0; top: 132px; justify-content: center; font-size: 34px; }
  .brand--back .brand__mark { width: 28px; height: 28px; }

  .divider {
    position: absolute; left: 307px; top: 70px; width: 1px; height: 110px;
    background: #4a4b4e;
  }

  .contact { position: absolute; left: 324px; top: 46px; color: var(--white); }
  .card--matte .contact { left: 308px; }
  .contact__name { font-size: 17px; font-weight: 700; letter-spacing: .3px; }
  .contact__name--light { font-weight: 400; }
  .contact__role { font-size: 15px; margin-top: 2px; }
  .contact__role--small { font-size: 13px; }
  .contact__lines { list-style: none; margin-top: 14px; font-size: 13px; line-height: 21px; }
  .contact__lines b { font-weight: 700; }
  .contact__email { font-size: 13px; margin-top: 10px; }

  .address {
    position: absolute; left: 0; right: 0; bottom: 12px; text-align: center;
    font-size: 13px; color: var(--ink);
  }

  .texture {
    position: absolute;
    background: radial-gradient(ellipse at center, #3a3b3e 0%, #1c1c1e 60%, var(--card-black) 100%);
  }
  .texture--top { left: 0; top: 0; width: 300px; height: 90px; }
  .texture--bottom { right: 0; bottom: 0; width: 260px; height: 110px; }
</style>
</head>
<body>
<main class="sheet">

  <p class="view-label" style="left:53px; top:22px;">front</p>
  <p class="view-label" style="left:628px; top:22px;">front-1</p>
  <p class="view-label" style="left:56px; top:405px;">back</p>
  <p class="view-label" style="left:624px; top:405px;">Back - 1</p>

  <!-- Front, carbon -->
  <section class="card card--carbon" style="left:53px; top:70px;">
    <svg class="card__wave" viewBox="0 0 526 301" preserveAspectRatio="none" aria-hidden="true">
      <path d="M340,254 C430,248 500,200 526,158 L526,196 C500,226 450,252 400,258 Z" fill="#000"/>
      <path d="M340,253 C430,247 498,200 526,160 L526,186 C498,222 445,250 380,255 Z" fill="var(--red)"/>
      <path d="M0,262 C60,236 150,226 260,244 C330,255 380,258 420,252 C470,242 508,216 526,198 L526,301 L0,301 Z" fill="var(--silver)"/>
    </svg>
    <div class="brand brand--front"><span class="brand__mark"></span>Vantorin Kitchens</div>
    <span class="divider"></span>
    <div class="contact">
      <p class="contact__name">MAREK SOLDEN</p>
      <p class="contact__role">President</p>
      <ul class="contact__lines">
        <li><b>phone</b> : 780.555.0147</li>
        <li><b>cell</b> : 780.555.0162</li>
        <li><b>fax</b> : 780.555.0119</li>
      </ul>
      <p class="contact__email">marek@vantorinkitchens.ca</p>
    </div>
    <p class="address">2810 - 48 Ave., Northfield, AB T0X 1K2</p>
  </section>

  <!-- Front, matte -->
  <section class="card card--matte" style="left:628px; top:70px;">
    <svg class="card__wave" viewBox="0 0 526 301" preserveAspectRatio="none" aria-hidden="true">
      <path d="M340,251 C430,245 500,200 526,158 L526,196 C500,226 450,252 400,258 Z" fill="#000"/>
      <path d="M340,250 C430,244 498,200 526,160 L526,186 C498,222 445,248 380,252 Z" fill="var(--red)"/>
      <path d="M0,262 C60,236 150,226 260,244 C330,255 380,258 420,252 C470,242 508,216 526,198 L526,301 L0,301 Z" fill="var(--silver-dark)"/>
    </svg>
    <div class="brand brand--front"><span class="brand__mark"></span>Vantorin Kitchens</div>
    <div class="contact">
      <p class="contact__name contact__name--light">DORIAN SOLDEN</p>
      <p class="contact__role contact__role--small">Director</p>
      <ul class="contact__lines">
        <li><b>phone</b> : 780.555.0147</li>
        <li><b>cell</b> : 780.555.0188</li>
        <li><b>fax</b> : 780.555.0119</li>
      </ul>
      <p class="contact__email">dorian@vantorinkitchens.ca</p>
    </div>
    <p class="address">2810 - 48 Ave., Northfield, AB T0X 1K2</p>
  </section>

  <!-- Back, carbon -->
  <section class="card card--carbon" style="left:56px; top:447px; height:299px;">
    <div class="brand brand--back"><span class="brand__mark"></span>Vantorin Kitchens</div>
  </section>

  <!-- Back, matte with perforated corners -->
  <section class="card card--matte" style="left:624px; top:446px; height:300px;">
    <div class="texture texture--top" role="img" aria-label="Perforated metal texture, top-left corner"></div>
    <div class="texture texture--bottom" role="img" aria-label="Perforated metal texture, bottom-right corner"></div>
    <div class="brand brand--back"><span class="brand__mark"></span>Vantorin Kitchens</div>
  </section>

</main>
</body>
</html>
```